Corporate Business Card

Very professional, Modern, Not to busy, include phone address email, website
(253) 617-4930, 18761 52nd Avenue S, Kent, WA 98047, martin@plumlinegroup.com, varkoworks.com

Target Market(s)

Manufacturing

Industry/Entity Type

Aero, machining, manufacturing, Off road racing

Contact Information for Business Card

Phone, address email, website

```html
<!DOCTYPE html>
<html lang="en">
<head>
<meta charset="utf-8">
<title>Varko Works – Business Card</title>
<link href="https://fonts.googleapis.com/css2?family=Titillium+Web:wght@400;600;700&display=swap" rel="stylesheet">
<style>
  :root {
    --navy: #173570;
    --red: #d42027;
    --white: #ffffff;
    --ink: #333840;
    --backdrop: #e9ecef;
  }
  * { margin: 0; padding: 0; box-sizing: border-box; }
  html, body {
    width: 1200px;
    height: 900px;
    overflow: hidden;
    background: var(--backdrop);
    font-family: "Titillium Web", sans-serif;
  }
  .business-card {
    position: absolute;
    left: 150px;
    top: 192px;
    width: 900px;
    height: 516px;
    border-radius: 18px;
    overflow: hidden;
    background: var(--white);
    box-shadow: 0 10px 30px rgba(0, 0, 0, 0.18);
  }
  .card-shapes {
    position: absolute;
    inset: 0;
  }
  .brand {
    position: absolute;
    left: 64px;
    top: 78px;
  }
  .brand-name {
    display: block;
    color: var(--white);
    font-weight: 700;
    font-size: 54px;
    line-height: 1;
    letter-spacing: 1px;
    text-transform: uppercase;
  }
  .brand-rule {
    display: block;
    margin-top: 18px;
    width: 166px;
    height: 2px;
    background: var(--white);
  }
  .holder {
    position: absolute;
    left: 62px;
    top: 268px;
  }
  .holder-name {
    color: var(--white);
    font-weight: 700;
    font-size: 35px;
    line-height: 1.1;
    text-transform: uppercase;
  }
  .holder-title {
    color: var(--red);
    font-weight: 400;
    font-size: 21px;
    line-height: 1.3;
  }
  .contact-list {
    position: absolute;
    right: 58px;
    top: 266px;
    list-style: none;
    color: var(--ink);
    font-size: 20px;
    line-height: 30px;
    text-align: right;
  }
  .contact-item {
    display: flex;
    justify-content: flex-end;
    align-items: flex-start;
    gap: 16px;
  }
  .contact-item + .contact-item { margin-top: 0; }
  .contact-item.address { margin-bottom: 12px; }
  .contact-icon {
    width: 16px;
    height: 16px;
    margin-top: 7px;
    flex: none;
    fill: var(--navy);
  }
</style>
</head>
<body>
  <section class="business-card">
    <svg class="card-shapes" width="900" height="516" viewBox="0 0 900 516" aria-hidden="true">
      <polygon points="0,0 838,0 176,516 0,516" fill="var(--navy)"/>
      <polygon points="829,516 900,516 900,458" fill="var(--red)"/>
    </svg>

    <div class="brand">
      <span class="brand-name">Varko Works</span>
      <span class="brand-rule"></span>
    </div>

    <div class="holder">
      <h1 class="holder-name">Daniel Brooks</h1>
      <p class="holder-title">Managing Director</p>
    </div>

    <ul class="contact-list">
      <li class="contact-item address">
        <span>18761 52nd Avenue S<br>Kent, WA 98047</span>
        <svg class="contact-icon" viewBox="0 0 16 16" aria-hidden="true"><path d="M8 0a5.5 5.5 0 0 0-5.5 5.5C2.5 9.6 8 16 8 16s5.5-6.4 5.5-10.5A5.5 5.5 0 0 0 8 0zm0 7.7a2.2 2.2 0 1 1 0-4.4 2.2 2.2 0 0 1 0 4.4z"/></svg>
      </li>
      <li class="contact-item">
        <span>(253) 617-4930</span>
        <svg class="contact-icon" viewBox="0 0 16 16" aria-hidden="true"><path d="M3.6 1 5.8 3.9 4.5 5.6c.9 2.2 2.6 3.9 4.8 4.9l1.6-1.4 3 2.1-1.1 2.9C7.4 14 2 8.6 1.9 3.2z"/><path d="M9.5 1.5a5 5 0 0 1 5 5h-1.3a3.7 3.7 0 0 0-3.7-3.7zm0 2.6a2.4 2.4 0 0 1 2.4 2.4h-1.2a1.2 1.2 0 0 0-1.2-1.2z"/></svg>
      </li>
      <li class="contact-item">
        <span>martin@plumlinegroup.com</span>
        <svg class="contact-icon" viewBox="0 0 16 16" aria-hidden="true"><path d="M1 3h14v1.2L8 8.6 1 4.2z"/><path d="M1 5.6l7 4.4 7-4.4V13H1z"/></svg>
      </li>
      <li class="contact-item">
        <span>www.varkoworks.com</span>
        <svg class="contact-icon" viewBox="0 0 16 16" aria-hidden="true"><path d="M8 0a8 8 0 1 0 0 16A8 8 0 0 0 8 0zm5.4 5H11a11 11 0 0 0-1-3.4A6.1 6.1 0 0 1 13.4 5zM8 1.9c.6.8 1.1 1.9 1.3 3.1H6.7C6.9 3.8 7.4 2.7 8 1.9zM1.9 9.5a6 6 0 0 1 0-3h2.6a13 13 0 0 0 0 3zm.7 1.5H5a11 11 0 0 0 1 3.4A6.1 6.1 0 0 1 2.6 11zM5 5H2.6A6.1 6.1 0 0 1 6 1.6 11 11 0 0 0 5 5zm3 9.1c-.6-.8-1.1-1.9-1.3-3.1h2.6c-.2 1.2-.7 2.3-1.3 3.1zm1.6-4.6H6.4a11 11 0 0 1 0-3h3.2a11 11 0 0 1 0 3zm.4 4.9a11 11 0 0 0 1-3.4h2.4a6.1 6.1 0 0 1-3.4 3.4zm1.5-4.9a13 13 0 0 0 0-3h2.6a6 6 0 0 1 0 3z"/></svg>
      </li>
    </ul>
  </section>
</body>
</html>
```